Website for IT consulting Company

I need a website upgrade, the existing site content is ok, I would also like to add a testimonial page, the site should be something that is easy for us to update content. You use the content from www.kelvanbrook.com as an example. I will also post update logo and artwork. I also need a contact form with some type of validation or captcha.

I added Coded to the Project

Please omit Address maps

Target Market(s)

small business, service oriented companies. We provide IT Consulting, support and mangement

Industry/Entity Type

Information Technology

Coding

Number of Pages Required

1 page

Font styles to use
Serif
Sans Serif

Requirements
Must have
• Contain logo attached, and content from existing web site www.kelvanbrook.com.
• Also need to update content easily, and be movable to different platforms.
• There is a catch phrase
• "Let us worry about your technology…” “ so you don’t have to!”
• Should be included.
Nice to have
• Testimonial page, Project page where we can post new and past projects and pictures
Should not have
• none

```html
<!DOCTYPE html>
<html lang="en">
<head>
<meta charset="utf-8">
<title>Kelvanbrook Development Group</title>
<link rel="stylesheet" href="https://fonts.googleapis.com/css2?family=Exo+2:ital,wght@0,700;0,800;1,700;1,800&family=Arimo:ital,wght@0,400;0,700;1,400&family=Tinos&display=swap">
<style>
:root{
  --black:#050505;
  --blue:#1a8ad4;
  --blue-dark:#0d6fb5;
  --blue-light:#38a9ea;
  --ink:#1b1b1b;
  --grey-bg:#f2f2f2;
  --grey-band:#a9a9ab;
  --footer:#2b2b2d;
  --white:#ffffff;
  --line:#9a9a9a;
}
*{margin:0;padding:0;box-sizing:border-box}
html,body{width:1200px;height:2711px;overflow:hidden}
body{position:relative;font-family:"Arimo",Arial,sans-serif;color:var(--ink);background:var(--white)}
section,header,nav,footer{position:absolute;left:0;width:1200px}
.abs{position:absolute}
.display{font-family:"Exo 2",sans-serif;font-weight:800}

/* header */
.topbar{top:0;height:125px;background:var(--black)}
.brand{left:82px;top:34px;display:flex;align-items:center;gap:14px}
.brand-square{width:46px;height:46px;background:var(--blue)}
.brand-name{font-family:"Exo 2",sans-serif;font-weight:800;font-size:48px;color:var(--white);letter-spacing:1px}
.follow{right:75px;top:17px;display:flex;align-items:center;gap:10px;color:var(--white);font:italic 700 18px "Exo 2",sans-serif}
.social{width:26px;height:26px;background:#8d8d8d;border-radius:3px}
.contact-top{right:75px;top:68px;display:flex;align-items:center;gap:14px;color:var(--white);font:italic 700 21px "Exo 2",sans-serif}
.icon-box{width:38px;height:38px;background:var(--blue);border-radius:4px;display:flex;align-items:center;justify-content:center}

/* nav */
.mainnav{top:125px;height:57px;background:linear-gradient(#2aa0e6,#127cc6)}
.mainnav a{position:absolute;top:17px;font:italic 800 20px "Exo 2",sans-serif;color:var(--white);text-decoration:none;letter-spacing:.5px}
.mainnav a.current{color:#0b2e4c}

/* hero */
.hero{top:182px;height:532px;background:linear-gradient(180deg,#9aa3ab 0%,#6d757d 35%,#4c5257 70%,#3a3e42 100%)}
.hero-line{left:0;width:100%;text-align:center;font:italic 800 33px "Exo 2",sans-serif;color:var(--white)}
.hero-line.accent{color:var(--blue-light)}
.dots{left:570px;top:508px;display:flex;gap:6px}
.dots span{width:10px;height:10px;border-radius:50%;background:#9b9b9b}
.dots span.on{background:var(--white)}

/* welcome */
.welcome{top:714px;height:293px;text-align:center}
.section-title{left:0;width:100%;text-align:center;font:800 28px "Exo 2",sans-serif;color:var(--ink);letter-spacing:.5px}
.section-title em{font-style:normal;color:var(--blue)}
.rule{left:560px;width:80px;height:3px;background:var(--blue)}
.intro{left:99px;top:108px;width:1016px;font-size:14.5px;line-height:26.5px;color:#222}
.btn{left:528px;top:211px;width:153px;height:38px;background:var(--blue);color:var(--white);font:17px "Tinos",serif;display:flex;align-items:center;justify-content:center}

/* services */
.services{top:1007px;height:574px;background:var(--grey-bg)}
.svc-label{font:italic 800 16px "Exo 2",sans-serif;color:var(--ink);line-height:18px}

/* it support */
.support{top:1581px;height:394px;background:linear-gradient(180deg,#cfcfd0 0%,#a3a3a5 60%,#8d8d8f 100%)}
.support .section-title em{color:var(--white)}
.card{top:145px;width:335px;height:186px;box-shadow:0 4px 8px rgba(0,0,0,.45)}
.card-caption{position:absolute;left:0;bottom:0;width:100%;height:38px;background:rgba(0,0,0,.6);color:var(--white);font:italic 700 18px "Exo 2",sans-serif;display:flex;align-items:center;justify-content:center}

/* testimonials */
.testimonials{top:1975px;height:362px}
.quote{left:210px;top:152px;width:780px;text-align:center;font:italic 15px/27px "Arimo",sans-serif;color:#222}
.author{left:0;width:100%;text-align:center;font-weight:700}

/* footer */
.footer{top:2337px;height:329px;background:linear-gradient(180deg,#3a3b3e,#242527)}
.col-title{top:60px;font:italic 800 18px "Exo 2",sans-serif;color:var(--white)}
.col-title em{color:var(--blue-light)}
.links{left:85px;top:100px;list-style:none;color:var(--white);font-size:14px;line-height:25px}
.links li::before{content:"•";color:var(--blue-light);margin-right:12px}
.divider{top:60px;width:1px;height:220px;background:#555}
.addr{left:286px;top:100px;color:var(--white);font-size:14px;line-height:22px}
.crow{left:286px;display:flex;align-items:center;gap:20px;color:var(--white);font-size:14px}
.field{left:600px;width:222px;background:var(--white);font-size:12px;color:#444;padding:6px}
.submit{left:604px;top:253px;width:85px;height:27px;background:var(--blue);color:var(--white);font:800 14px "Exo 2",sans-serif;display:flex;align-items:center;justify-content:center}
.bottombar{top:2666px;height:45px;background:var(--blue-dark)}
.copy{left:85px;top:14px;color:var(--white);font:italic 700 14px "Exo 2",sans-serif}
</style>
</head>
<body>

<header class="topbar">
  <div class="abs brand"><span class="brand-square"></span><span class="brand-name">KELVANBROOK</span></div>
  <div class="abs follow">Follow Us On <span class="social"></span><span class="social"></span><span class="social"></span><span class="social"></span></div>
  <div class="abs contact-top">
    <span class="icon-box"><svg width="20" height="20" viewBox="0 0 24 24"><path fill="#fff" d="M6.6 10.8a15 15 0 0 0 6.6 6.6l2.2-2.2c.3-.3.7-.4 1-.2 1.1.4 2.3.6 3.6.6.6 0 1 .4 1 1V20c0 .6-.4 1-1 1A17 17 0 0 1 3 4c0-.6.4-1 1-1h3.5c.6 0 1 .4 1 1 0 1.3.2 2.5.6 3.6.1.3 0 .7-.2 1z"/></svg></span>
    (555) 014-2290
    <span class="icon-box" style="margin-left:4px"><svg width="22" height="22" viewBox="0 0 24 24"><circle cx="12" cy="8" r="4" fill="#fff"/><path fill="#fff" d="M4 21c0-4.4 3.6-7 8-7s8 2.6 8 7z"/></svg></span>
    SUPPORT
  </div>
</header>

<nav class="mainnav">
  <a class="current" style="left:96px">HOME</a>
  <a style="left:219px">ABOUT US</a>
  <a style="left:376px">SERVICES</a>
  <a style="left:533px">PROJECTS</a>
  <a style="left:694px">CLIENTS</a>
  <a style="left:838px">CAREERS</a>
  <a style="left:988px">CONTACT US</a>
</nav>

<section class="hero" role="img" aria-label="Aerial photograph of a downtown skyline with office towers">
  <p class="abs hero-line" style="top:290px">Let Us Worry About Your Technology...</p>
  <p class="abs hero-line accent" style="top:338px">So You Don’t Have To!</p>
  <div class="abs dots"><span></span><span></span><span></span><span class="on"></span></div>
</section>

<section class="welcome">
  <h1 class="abs section-title" style="top:40px">WELCOME TO KELVANBROOK <em>DEVELOPMENT GROUP, INC</em></h1>
  <div class="abs rule" style="top:83px"></div>
  <p class="abs intro">Kelvanbrook Development Group, Inc. was established in 1991. Our mission is helping businesses and individuals realize a Return on Investment by implementing today’s advanced technologies. As a small business we understand the importance of technology and personalized attention. Every member of our support team has worked with both large and small companies supporting a multitude of applications, networks and environments.</p>
  <div class="abs btn">Read More &rarr;</div>
</section>

<section class="services">
  <h2 class="abs section-title" style="top:52px">OUR <em>SERVICES</em></h2>
  <div class="abs rule" style="top:95px"></div>
  <svg class="abs" style="left:0;top:0" width="1200" height="574" viewBox="0 0 1200 574">
    <g stroke="#8a8a8a" stroke-width="2" stroke-dasharray="3 4" fill="none">
      <line x1="266" y1="490" x2="374" y2="515"/><line x1="307" y1="380" x2="401" y2="438"/>
      <line x1="385" y1="291" x2="452" y2="376"/><line x1="490" y1="229" x2="528" y2="333"/>
      <line x1="609" y1="208" x2="609" y2="322"/><line x1="726" y1="231" x2="688" y2="333"/>
      <line x1="829" y1="291" x2="764" y2="376"/><line x1="909" y1="376" x2="817" y2="438"/>
      <line x1="952" y1="491" x2="840" y2="515"/>
    </g>
    <path d="M366 574 A243 250 0 0 1 852 574" fill="none" stroke="#9c9c9c" stroke-width="9"/>
    <g fill="#fff" stroke="#8a8a8a" stroke-width="3">
      <circle cx="374" cy="515" r="9"/><circle cx="401" cy="438" r="9"/><circle cx="452" cy="376" r="9"/>
      <circle cx="528" cy="333" r="9"/><circle cx="609" cy="322" r="9"/><circle cx="688" cy="333" r="9"/>
      <circle cx="764" cy="376" r="9"/><circle cx="817" cy="438" r="9"/><circle cx="840" cy="515" r="9"/>
    </g>
    <defs><linearGradient id="bubble" x1="0" y1="0" x2="0" y2="1"><stop offset="0" stop-color="#3aaaf0"/><stop offset="1" stop-color="#0c70b8"/></linearGradient></defs>
    <g fill="url(#bubble)" stroke="#fff" stroke-width="3">
      <circle cx="266" cy="490" r="49"/><circle cx="307" cy="380" r="49"/><circle cx="385" cy="291" r="49"/>
      <circle cx="490" cy="229" r="49"/><circle cx="609" cy="208" r="49"/><circle cx="726" cy="231" r="49"/>
      <circle cx="829" cy="291" r="49"/><circle cx="909" cy="376" r="49"/><circle cx="952" cy="491" r="49"/>
    </g>
    <g fill="#fff" stroke="none">
      <rect x="246" y="474" width="40" height="28" rx="3"/><rect x="256" y="504" width="20" height="4"/>
      <circle cx="300" cy="370" r="10"/><path d="M282 402c0-12 8-18 18-18s18 6 18 18z"/><rect x="314" y="378" width="14" height="10"/>
      <path d="M378 312l7-30 7 30h-4l-3-12-3 12z"/><circle cx="385" cy="279" r="5"/>
      <circle cx="490" cy="229" r="22"/><rect x="481" y="218" width="6" height="22" fill="#1a8ad4"/><rect x="493" y="218" width="6" height="22" fill="#1a8ad4"/>
      <rect x="589" y="186" width="40" height="12" rx="2"/><rect x="589" y="202" width="40" height="12" rx="2"/><rect x="589" y="218" width="28" height="12" rx="2"/>
      <rect x="704" y="215" width="32" height="24" rx="2"/><rect x="738" y="220" width="12" height="22" rx="2"/><rect x="712" y="242" width="16" height="4"/>
      <rect x="813" y="278" width="24" height="24" rx="3"/><rect x="837" y="300" width="8" height="14"/>
      <rect x="889" y="380" width="40" height="12" rx="3"/><circle cx="909" cy="368" r="4"/>
      <path d="M932 472l20-7 20 7v14c0 14-10 22-20 26-10-4-20-12-20-26z"/>
    </g>
    <text x="609" y="512" text-anchor="middle" font-family="Exo 2, sans-serif" font-weight="800" font-size="52" fill="#6f6f72">KELVANBROOK</text>
  </svg>
  <div class="abs svc-label" style="right:1001px;top:492px;text-align:right">DESKTOP<br>SUPPORT</div>
  <div class="abs svc-label" style="right:956px;top:360px;text-align:right">NETWORK<br>ADMINISTRATION</div>
  <div class="abs svc-label" style="right:878px;top:268px;text-align:right">TELECOMMUNICATIONS</div>
  <div class="abs svc-label" style="right:761px;top:192px;text-align:right">AUDIO/VIDEO MULTIMEDIA</div>
  <div class="abs svc-label" style="left:464px;width:300px;top:135px;text-align:center">DISASTER RECOVERY</div>
  <div class="abs svc-label" style="left:777px;top:182px">WEB DESIGN</div>
  <div class="abs svc-label" style="left:893px;top:268px">NETWORK CABLING</div>
  <div class="abs svc-label" style="left:976px;top:360px">WIRELESS<br>NETWORKS</div>
  <div class="abs svc-label" style="left:1008px;top:474px">ANTIVIRUS<br>SOLUTIONS</div>
</section>

<section class="support">
  <h2 class="abs section-title" style="top:60px">IT SUPPORT <em>SOLUTION</em></h2>
  <div class="abs rule" style="top:103px;background:var(--white)"></div>
  <svg class="abs" style="left:36px;top:184px" width="20" height="36" viewBox="0 0 20 36"><path d="M18 2L3 18l15 16" fill="none" stroke="#6a6a6a" stroke-width="2"/></svg>
  <svg class="abs" style="left:1140px;top:184px" width="20" height="36" viewBox="0 0 20 36"><path d="M2 2l15 16L2 34" fill="none" stroke="#6a6a6a" stroke-width="2"/></svg>
  <div class="abs card" style="left:81px;background:linear-gradient(135deg,#3b5f8a,#8aa6c2 60%,#2d4560)" role="img" aria-label="Photo of technicians in a server room"><div class="card-caption">Managed IT Solutions</div></div>
  <div class="abs card" style="left:434px;background:linear-gradient(135deg,#0f2b44,#2f6d96 55%,#0d1e2e)" role="img" aria-label="Photo of hands holding a tablet with glowing data"><div class="card-caption">Remote Diagnostics &amp; Support</div></div>
  <div class="abs card" style="left:786px;background:linear-gradient(135deg,#2a3440,#56616c 55%,#1f262e)" role="img" aria-label="Photo of a man sketching a process diagram on a chalkboard"><div class="card-caption">Infrastructure Design &amp; Installation</div></div>
</section>

<section class="testimonials">
  <h2 class="abs section-title" style="top:52px">CLIENTS <em>TESTIMONIALS</em></h2>
  <div class="abs rule" style="top:95px"></div>
  <svg class="abs" style="left:110px;top:195px" width="30" height="56" viewBox="0 0 30 56"><path d="M28 2L3 28l25 26" fill="none" stroke="#aaa" stroke-width="2"/></svg>
  <svg class="abs" style="left:1052px;top:195px" width="30" height="56" viewBox="0 0 30 56"><path d="M2 2l25 26L2 54" fill="none" stroke="#aaa" stroke-width="2"/></svg>
  <p class="abs quote"><span style="font-size:34px;color:#bbb;vertical-align:-8px">“</span> Lorem ipsum dolor sit amet, consectetuer adipiscing elit, sed diam nonummy nibh euismod tinciduntut laoreet dolore magna aliquam erat volutpat. Ut wisi enim ad minim veniam, quis nostrud exercimori mornkle tation ullamcorper suscipit lobortis nisl ut aliquip ex ea commodo consequat. <span style="font-size:34px;color:#bbb;vertical-align:-8px">”</span></p>
  <p class="abs author" style="top:258px;font-size:17px">Renata V.</p>
  <p class="abs author" style="top:285px;font-size:14px">Fairview, OR</p>
</section>

<footer class="footer">
  <h3 class="abs col-title" style="left:85px">Quick <em>Links</em></h3>
  <ul class="abs links"><li>Home</li><li>About Us</li><li>Services</li><li>Projects</li><li>Clients</li><li>Careers</li><li>Contact Us</li></ul>
  <div class="abs divider" style="left:245px"></div>
  <h3 class="abs col-title" style="left:286px">Contact <em>Details</em></h3>
  <p class="abs addr">Kelvanbrook Development Group, Inc.<br><br>418 Marlow Ave.<br>Austin, Texas 78701</p>
  <div class="abs crow" style="top:213px"><svg width="16" height="16" viewBox="0 0 24 24"><path fill="#38a9ea" d="M6.6 10.8a15 15 0 0 0 6.6 6.6l2.2-2.2c.3-.3.7-.4 1-.2 1.1.4 2.3.6 3.6.6.6 0 1 .4 1 1V20c0 .6-.4 1-1 1A17 17 0 0 1 3 4c0-.6.4-1 1-1h3.5c.6 0 1 .4 1 1 0 1.3.2 2.5.6 3.6.1.3 0 .7-.2 1z"/></svg>(555) 014-2290</div>
  <div class="abs crow" style="top:238px"><svg width="16" height="16" viewBox="0 0 24 24"><rect x="3" y="8" width="18" height="10" rx="2" fill="#38a9ea"/><rect x="7" y="3" width="10" height="6" fill="#38a9ea"/></svg>(555) 014-2290</div>
  <div class="abs crow" style="top:266px"><svg width="16" height="16" viewBox="0 0 24 24"><rect x="2" y="5" width="20" height="14" rx="2" fill="#38a9ea"/><path d="M2 6l10 7 10-7" fill="none" stroke="#2b2b2d" stroke-width="2"/></svg>info@kelvanbrook.com</div>
  <div class="abs divider" style="left:565px"></div>
  <h3 class="abs col-title" style="left:600px">Quick <em>Inquiry</em></h3>
  <div class="abs field" style="top:105px;height:34px">Name</div>
  <div class="abs field" style="top:145px;height:33px">Email</div>
  <div class="abs field" style="top:183px;height:59px">Message</div>
  <div class="abs submit">SUBMIT</div>
</footer>

<div class="abs bottombar">
  <p class="abs copy">Copyright © 2017 Kelvanbrook Development Group, Inc. All Rights Reserved.</p>
  <div class="abs follow" style="top:9px">Follow Us On <span class="social"></span><span class="social"></span><span class="social"></span><span class="social"></span></div>
</div>

</body>
</html>
```